sydney wedding photography business needs a business card design

we need a business card design for a sydney based wedding photography and videography business. our business name is :golden hour studio and film. our target clients are 24-35 yrs female. our style is candid, organic, natural, dynamic. we are a team of young photographers and videographers, and help brides to create memories that they will cherish for the rest of their lives. the logo will be provided. we want an elegant design that reflects our style, and also want to give a great impression to our clients that we are one of the best studios in sydney and our brand means quality and premium service.

Target Market(s)

bride to be, 24-35 years old, living in sydney and surrunding areas

Industry/Entity Type

Wedding Photography

Contact Information for Business Card

address: 57 tarrant street, glenmore nsw 2047
mobile: 0431872259
phone: (02) 9163 2408
info@tidewillowstudio.net.au
www.tidewillowstudio.net.au
facebook:tidewillowweddings
instagram:tidewillowweddings

Font styles to use
Serif
Sans Serif

Requirements
Nice to have
• maybe add my slogan"memories beyond eternity" if the layout looks good
Should not have
• no black color, not good idea for wedding biz card

```html
<!DOCTYPE html>
<html lang="en">
<head>
<meta charset="utf-8">
<title>Golden Hour Studio and Film – Business Card</title>
<link rel="stylesheet" href="https://fonts.googleapis.com/css2?family=Arimo:wght@400;500&display=swap">
<style>
  :root {
    --page-bg: #e6ddd3;
    --card-deep: #3b2a22;
    --card-mid: #4d372c;
    --card-glow: #6a4d3d;
    --card-border: #7a5a47;
    --gold: #d9a04a;
    --gold-deep: #c48a3a;
    --rose-gold: #e0aea6;
    --text-light: #f4ece4;
    --text-soft: #d9cbbf;
    --text-muted: #bfae9f;
  }
  * { margin: 0; padding: 0; box-sizing: border-box; }
  html, body {
    width: 1200px;
    height: 969px;
    overflow: hidden;
    background: var(--page-bg);
    font-family: "Arimo", Arial, sans-serif;
  }
  .canvas {
    position: relative;
    width: 1200px;
    height: 969px;
  }
  .business-card {
    position: absolute;
    left: 100px;
    top: 201px;
    width: 1000px;
    height: 567px;
    background:
      radial-gradient(ellipse at 22% 30%, var(--card-glow) 0%, var(--card-mid) 35%, var(--card-deep) 75%);
    box-shadow: 0 18px 40px rgba(60, 40, 30, 0.25);
    border: 1px solid var(--card-border);
  }
  .brand-name {
    position: absolute;
    right: 58px;
    top: 78px;
    font-size: 40px;
    font-weight: 400;
    color: var(--gold);
    white-space: nowrap;
  }
  .holder-name {
    position: absolute;
    left: 60px;
    top: 302px;
    font-size: 33px;
    font-weight: 500;
    color: var(--gold);
  }
  .holder-title {
    position: absolute;
    left: 60px;
    top: 343px;
    font-size: 26px;
    color: var(--text-soft);
  }
  .social-marks {
    position: absolute;
    right: 60px;
    top: 344px;
    display: flex;
    gap: 6px;
  }
  .social-marks span {
    width: 28px;
    height: 28px;
    border-radius: 50%;
    background: var(--gold-deep);
  }
  .divider {
    position: absolute;
    left: 60px;
    right: 60px;
    top: 387px;
    height: 2px;
    background: var(--gold-deep);
  }
  .contact {
    position: absolute;
    left: 60px;
    font-size: 25px;
    white-space: nowrap;
  }
  .contact-address { top: 404px; color: var(--text-light); }
  .contact-phones { top: 444px; color: var(--rose-gold); }
  .contact-web { top: 482px; color: var(--text-muted); }
  .label-gold { color: var(--gold-deep); }
</style>
</head>
<body>
<main class="canvas">
  <section class="business-card" aria-label="Golden Hour Studio and Film business card">
    <div class="brand-name">golden hour studio and film</div>

    <div class="holder-name">Mara Ellison</div>
    <div class="holder-title">President</div>

    <div class="social-marks" aria-label="social links">
      <span></span><span></span>
    </div>

    <div class="divider"></div>

    <p class="contact contact-address">57 tarrant street, glenmore nsw 2047</p>
    <p class="contact contact-phones"><span class="label-gold">P :</span> (02) 9163 2408 &nbsp;<span class="label-gold">M :</span> (04) 3187 2259</p>
    <p class="contact contact-web"><span class="label-gold">E :</span> info@tidewillowstudio.net.au &nbsp;<span class="label-gold">W :</span> tidewillowstudio.net.au</p>
  </section>
</main>
</body>
</html>
```